Quillmarsh Property Solutions need a business card design

Hello guys. We would need a business card design asap please.
We are a start up property investment business based in London UK specialised in buying, selling, managing and letting properties and helping distressed property owners.
The name of our Business is Quillmarsh, the logo symbolises the four fundamental elements of the world (earth, air, fire and water) and so it stands for strength, stability, longevity.
We would like the business card to communicate professionalism and reliability. Many many thanks indeed for your work.

Details:

1.) Rosalind Updike
Property Investor
Mobile: +44(0)7700123456
Email: rosalind.quillmarsh@mailbox-example.com

2.) Dominic Updike
Property Investor
Mobile: +44(0)7700987654
Email: dominic.quillmarsh@mailbox-example.com

```html
<!DOCTYPE html>
<html lang="en">
<head>
<meta charset="utf-8">
<title>Quillmarsh Property Solutions – Business Card</title>
<link rel="stylesheet" href="https://fonts.googleapis.com/css2?family=Jost:wght@600&family=Open+Sans:wght@400;600&display=swap">
<style>
  :root {
    --backdrop: #e4e5ea;
    --card: #ffffff;
    --ink: #111111;
    --band-red: #c0272f;
    --name-blue: #2a4f9c;
    --role-green: #2f6b3a;
    --on-band: #ffffff;
  }
  * { margin: 0; padding: 0; box-sizing: border-box; }
  html, body {
    width: 1200px; height: 987px; overflow: hidden;
    background: var(--backdrop);
  }
  .canvas { position: relative; width: 1200px; height: 987px; }

  .card {
    position: absolute;
    width: 580px; height: 360px;
    background: var(--card);
    border-radius: 22px;
    box-shadow: 0 10px 28px rgba(0,0,0,0.16);
    overflow: hidden;
  }

  /* Back of card */
  .card--back { left: 570px; top: 70px; }
  .card--back .wordmark {
    position: absolute; left: 0; right: 0; top: 120px;
    text-align: center;
    font-family: 'Jost', sans-serif; font-weight: 600; color: var(--ink);
  }
  .card--back .wordmark__name { font-size: 62px; letter-spacing: 3px; line-height: 1; }
  .card--back .wordmark__tag { font-size: 24px; letter-spacing: 2px; margin-top: 8px; }

  /* Front of card */
  .card--front { left: 50px; top: 540px; }
  .card--front .wordmark {
    position: absolute; left: 0; right: 0; top: 70px;
    text-align: center;
    font-family: 'Jost', sans-serif; font-weight: 600; color: var(--ink);
  }
  .card--front .wordmark__name { font-size: 36px; letter-spacing: 2px; line-height: 1; }
  .card--front .wordmark__tag { font-size: 14px; letter-spacing: 1.5px; margin-top: 5px; }

  .contact-band {
    position: absolute; left: 0; right: 0; top: 185px; height: 62px;
    background: var(--band-red);
    display: flex; align-items: center; gap: 10px;
    padding-left: 34px;
    font-family: 'Open Sans', sans-serif; font-size: 15px; color: var(--on-band);
  }
  .contact-band .item { display: flex; align-items: center; gap: 6px; }
  .contact-band svg { width: 14px; height: 14px; fill: var(--on-band); }
  .contact-band .divider { opacity: 0.8; }

  .holder {
    position: absolute; left: 34px; top: 268px;
    font-family: 'Open Sans', sans-serif; font-size: 21px;
  }
  .holder__name { color: var(--name-blue); font-weight: 600; }
  .holder__role { color: var(--role-green); font-weight: 400; }
</style>
</head>
<body>
<div class="canvas">

  <section class="card card--back">
    <div class="wordmark">
      <div class="wordmark__name">QUILLMARSH</div>
      <div class="wordmark__tag">PROPERTY SOLUTIONS</div>
    </div>
  </section>

  <section class="card card--front">
    <div class="wordmark">
      <div class="wordmark__name">QUILLMARSH</div>
      <div class="wordmark__tag">PROPERTY SOLUTIONS</div>
    </div>

    <div class="contact-band">
      <span class="item">
        <svg viewBox="0 0 14 14" aria-hidden="true"><path d="M4 0h6a1 1 0 0 1 1 1v12a1 1 0 0 1-1 1H4a1 1 0 0 1-1-1V1a1 1 0 0 1 1-1zm0 2v9h6V2zm3 9.6a.8.8 0 1 0 0 1.6.8.8 0 0 0 0-1.6z"/></svg>
        +44(0)7700987654
      </span>
      <span class="divider">|</span>
      <span class="item">
        <svg viewBox="0 0 14 14" aria-hidden="true"><path d="M1 3h12v8H1zm1 1v.4l5 3.3 5-3.3V4zm0 1.6V10h10V5.6L7 8.9z"/></svg>
        dominic.quillmarsh@mailbox-example.com
      </span>
    </div>

    <div class="holder">
      <span class="holder__name">Dominic Updike,</span>
      <span class="holder__role">Property Investor</span>
    </div>
  </section>

</div>
</body>
</html>
```